Wealth Education Business Needs Sharp Business Card Design

We need a business card design for a recently launched investor education business called Harbor Crest.

The final design should promote security, empowerment, self improvement and financial gain. The card will ideally promote the stature of the business.

For more information and colours please visit harborcrest.com.au

Target Market(s)

Corporate executives and high net worth individuals

Industry/Entity Type

Education

Contact Information for Business Card

```html
<!DOCTYPE html>
<html lang="en">
<head>
<meta charset="utf-8">
<title>Harbor Crest – Business Card</title>
<link rel="stylesheet" href="https://fonts.googleapis.com/css2?family=Lato:wght@400;700;900&display=swap">
<style>
  :root {
    --page-bg: #d8d5d0;
    --card-bg: #eef1f2;
    --card-edge: #c9d0d3;
    --ink: #2e2f31;
    --ink-soft: #3a3c3f;
    --green: #5f9c2f;
    --teal: #2a8f9a;
    --band-start: #2ea1d4;
    --band-end: #8fcbe6;
    --band-tail: #cfe7f2;
  }
  * { box-sizing: border-box; margin: 0; padding: 0; }
  html, body {
    width: 1200px; height: 970px; overflow: hidden;
    background: var(--page-bg);
    font-family: "Lato", Arial, sans-serif;
  }
  .business-card {
    position: absolute;
    left: 80px; top: 197px;
    width: 1040px; height: 575px;
    background: var(--card-bg);
    border: 2px solid var(--card-edge);
    border-radius: 34px;
    overflow: hidden;
  }
  .brand {
    position: absolute; left: 54px; top: 128px;
    display: flex; align-items: center; gap: 22px;
  }
  .brand-mark {
    width: 34px; height: 34px; border-radius: 50%;
    background: var(--teal);
  }
  .brand-name {
    font-weight: 700; font-size: 44px; letter-spacing: 7px;
    color: var(--ink);
  }
  .person {
    position: absolute; right: 52px; top: 108px; text-align: right;
  }
  .person-name {
    font-weight: 900; font-size: 37px; color: var(--green); line-height: 1.1;
  }
  .person-title {
    font-weight: 700; font-size: 25px; color: var(--ink); margin-top: 6px;
  }
  .contact-band {
    position: absolute; left: 0; top: 254px; width: 100%; height: 221px;
    background: linear-gradient(90deg, var(--band-start) 0%, #4aafdb 55%, var(--band-end) 100%);
  }
  .contact-band::after {
    content: ""; position: absolute; left: 0; right: 0; bottom: -20px; height: 20px;
    background: linear-gradient(180deg, var(--band-tail), rgba(207,231,242,0));
  }
  .contact-list {
    position: absolute; left: 48px; top: 50px; list-style: none;
  }
  .contact-list li {
    display: flex; align-items: center; gap: 14px;
    font-size: 27px; color: var(--ink-soft); height: 35px;
  }
  .icon { width: 24px; height: 24px; flex: none; }
  .address {
    position: absolute; left: 48px; top: 498px;
    display: flex; align-items: center; gap: 14px;
    font-size: 28px; color: var(--ink-soft);
  }
</style>
</head>
<body>
  <main class="business-card">
    <div class="brand">
      <span class="brand-mark"></span>
      <span class="brand-name">HARBOR CREST</span>
    </div>

    <div class="person">
      <div class="person-name">Marcus Hale</div>
      <div class="person-title">Director</div>
    </div>

    <section class="contact-band">
      <ul class="contact-list">
        <li>
          <svg class="icon" viewBox="0 0 24 24" aria-hidden="true"><path d="M3 9c0-3 4-5 9-5s9 2 9 5l-4 1-1-3H8L7 10 3 9z M6 12h12l2 8H4l2-8z" fill="var(--green)"/></svg>
          1300 555 018
        </li>
        <li>
          <svg class="icon" viewBox="0 0 24 24" aria-hidden="true"><rect x="6" y="2" width="12" height="20" rx="2" fill="none" stroke="var(--green)" stroke-width="2.2"/><circle cx="12" cy="18" r="1.3" fill="var(--green)"/></svg>
          +613 9555 0142
        </li>
        <li>
          <svg class="icon" viewBox="0 0 24 24" aria-hidden="true"><rect x="2" y="5" width="20" height="14" rx="2" fill="var(--green)"/><path d="M3 6l9 7 9-7" fill="none" stroke="#cfe7f2" stroke-width="1.6"/></svg>
          support@harborcrest.com.au
        </li>
        <li>
          <svg class="icon" viewBox="0 0 24 24" aria-hidden="true"><rect x="2" y="3" width="20" height="18" rx="2" fill="var(--green)"/><rect x="4" y="8" width="16" height="11" fill="#cfe7f2"/></svg>
          www.harborcrest.com.au
        </li>
      </ul>
    </section>

    <div class="address">
      <svg class="icon" viewBox="0 0 24 24" aria-hidden="true"><path d="M12 3L2 12h3v9h5v-6h4v6h5v-9h3L12 3z" fill="var(--green)"/></svg>
      Level 4, 72 Tidewater Lane, Melbourne VIC 3000
    </div>
  </main>
</body>
</html>
```